Business Card Design

We are a commercial real estate brokerage in San Francisco, leasing office buildings downtown.
I would like a clean, elegant look. Simple but powerful .

Industry/Entity Type

Business

Contact Information for Business Card

Derek Holloway
lic# 07258143
415.555.0172
derek@velt-commercial.example
velt-commercial.example

```html
<!DOCTYPE html>
<html lang="en">
<head>
<meta charset="utf-8">
<title>Velt Commercial — Business Card</title>
<link rel="stylesheet" href="https://fonts.googleapis.com/css2?family=Oswald:wght@300;400;500&display=swap">
<style>
  :root {
    --backdrop: #d9caa8;
    --card-white: #ffffff;
    --panel-grey: #e8e8e8;
    --brand-slate: #6a7b98;
    --text-grey: #8a8a8a;
    --icon-grey: #7c7c7c;
  }
  * { margin: 0; padding: 0; box-sizing: border-box; }
  html, body {
    width: 1200px;
    height: 510px;
    overflow: hidden;
    background: var(--backdrop);
  }
  .stage {
    position: relative;
    width: 1200px;
    height: 510px;
  }
  .business-card {
    position: absolute;
    left: 377px;
    top: 112px;
    width: 418px;
    height: 245px;
    background: var(--card-white);
    padding: 11px;
    display: flex;
    flex-direction: column;
    gap: 3px;
  }
  .identity-panel {
    background: var(--panel-grey);
    height: 115px;
    display: flex;
    flex-direction: column;
    align-items: center;
    padding-top: 22px;
  }
  .brand {
    display: flex;
    align-items: center;
    gap: 9px;
  }
  .brand-square {
    width: 30px;
    height: 30px;
    background: var(--brand-slate);
  }
  .brand-name {
    font-family: "Oswald", sans-serif;
    font-weight: 500;
    color: var(--brand-slate);
    text-transform: uppercase;
    line-height: 1;
  }
  .brand-name .word-main { display: block; font-size: 27px; letter-spacing: 0.5px; }
  .brand-name .word-sub { display: block; font-size: 12.5px; letter-spacing: 0.6px; margin-top: 2px; }
  .holder-name {
    margin-top: 22px;
    font-family: "Oswald", sans-serif;
    font-weight: 300;
    font-size: 18px;
    color: var(--text-grey);
    text-transform: uppercase;
    letter-spacing: 0.3px;
  }
  .contact-row {
    display: grid;
    grid-template-columns: repeat(4, 1fr);
    gap: 3px;
    height: 105px;
  }
  .contact-cell {
    background: var(--panel-grey);
    display: flex;
    flex-direction: column;
    align-items: center;
    justify-content: center;
    gap: 5px;
    padding-top: 6px;
  }
  .contact-icon {
    width: 11px;
    height: 11px;
    stroke: var(--icon-grey);
    fill: none;
    stroke-width: 1;
  }
  .contact-text {
    font-family: "Oswald", sans-serif;
    font-weight: 300;
    font-size: 7px;
    color: var(--text-grey);
    white-space: nowrap;
  }
  .contact-text.email { font-size: 6.3px; }
  .contact-cell.license { padding-top: 17px; }
</style>
</head>
<body>
<div class="stage">
  <div class="business-card">
    <div class="identity-panel">
      <div class="brand">
        <div class="brand-square"></div>
        <div class="brand-name">
          <span class="word-main">Velt</span>
          <span class="word-sub">Commercial</span>
        </div>
      </div>
      <div class="holder-name">Derek Holloway</div>
    </div>
    <div class="contact-row">
      <div class="contact-cell license">
        <span class="contact-text">lic# 07258143</span>
      </div>
      <div class="contact-cell">
        <svg class="contact-icon" viewBox="0 0 11 11" aria-hidden="true">
          <rect x="3" y="0.5" width="5" height="10" rx="1"/>
          <line x1="5" y1="9" x2="6" y2="9"/>
        </svg>
        <span class="contact-text">415.555.0172</span>
      </div>
      <div class="contact-cell">
        <svg class="contact-icon" viewBox="0 0 11 11" aria-hidden="true">
          <rect x="0.5" y="2" width="10" height="7"/>
          <polyline points="0.5,2 5.5,6 10.5,2"/>
        </svg>
        <span class="contact-text email">derek@velt-commercial.example</span>
      </div>
      <div class="contact-cell">
        <svg class="contact-icon" viewBox="0 0 11 11" aria-hidden="true">
          <circle cx="5.5" cy="5.5" r="5"/>
          <ellipse cx="5.5" cy="5.5" rx="2.2" ry="5"/>
          <line x1="0.5" y1="5.5" x2="10.5" y2="5.5"/>
        </svg>
        <span class="contact-text">velt-commercial.example</span>
      </div>
    </div>
  </div>
</div>
</body>
</html>
```